Scientific Web Site for KLORVEST

Professional Scientific / Service orientated web site, motto, new logos attached for viewing.

"We measure so the Business Owner can Manage" their environments.
Site needs to be be mobile friendly.

We provide a service to electronically measure cleanliness of any surface and a value added disinfecting fogging surface.

Reports showing locations, trending, tracking and randomized test plans ongoing audits will be made available..

NOTE: Although image of Corona Virus is current we don't wont it plastered through the web site, their is more than the current virus.

Home Page - Professional Scientific / Service Looking
About
Our Approach
Services
Residential
Commercial
Transportation
Gyms
Educational & Daycare
Real Estate - Open for inspections, End of Lease etc

Contact
Mobile #
Email
Form to leave their details

Links to social media, Facebook, Instagram
Reference Sites: Ranked in preference
www.brelmont.com.au
https://www.tidewellhygiene.co.uk/
https://www.mistrova.com/
https://www.zenplax.com.au/specialist-surface-disinfection/
https://www.artfolder.example/design/48172039
https://www.artfolder.example/design/51904476
https://www.artfolder.example/design/47318865

Target Market(s)

Commercial and professional Services

Font styles to use
Sans Serif

Requirements
Must have
• Wix Website
Clean fresh look with appropriate imaging
Web site is a company advertising that will hold static information and we will market through social media.
Nice to have
• Scientific look and feel
Should not have
• Prominent Corona Virus images or references

```html
<!DOCTYPE html>
<html lang="en">
<head>
<meta charset="utf-8">
<title>Klorvest</title>
<link rel="stylesheet" href="https://fonts.googleapis.com/css2?family=Outfit:wght@400;500;600&display=swap">
<style>
:root{
  --orange:#f26a1b;
  --ink:#1c1c1c;
  --body:#3a3a3a;
  --dark:#1f1b1c;
  --white:#ffffff;
  --dot:#c9c9c9;
  --line:#d6d6d6;
}
*{margin:0;padding:0;box-sizing:border-box}
html,body{width:1200px;height:3974px;overflow:hidden}
body{font-family:"Outfit",sans-serif;color:var(--body);background:var(--white);position:relative}
.abs{position:absolute}
.center{left:0;width:1200px;text-align:center}
.dots{position:absolute;left:1138px;display:flex;flex-direction:column;gap:19px}
.dots span{width:12px;height:12px;border-radius:50%;background:var(--dot)}
.dots span.on{background:var(--orange)}
.dots.light span{background:#fff}

/* hero */
.hero{top:0;left:0;width:1200px;height:714px;background:linear-gradient(120deg,#4a4c4f 0%,#6b6d6f 35%,#8a8c88 60%,#5e5a4a 100%)}
.hero::after{content:"";position:absolute;inset:0;background:rgba(0,0,0,.32)}
.logo{font-weight:500;letter-spacing:4px;font-size:28px}
.hero .logo{left:75px;top:80px;color:#fff;z-index:2}
.nav{top:65px;z-index:2;display:flex;left:570px}
.nav a{color:#fff;text-decoration:none;font-weight:600;font-size:16px;height:32px;line-height:32px;padding:0 16px}
.nav a.active{background:var(--orange);padding:0 22px}
.hero h1{top:345px;z-index:2;color:#fff;font-weight:600;font-size:46px;line-height:54px}

/* about */
.about{top:714px;left:0;width:1200px;height:424px;background:linear-gradient(200deg,#efe3fb 0%,#fff 22%)}
h2{font-weight:600;color:var(--ink);font-size:42px}
.about h2{top:57px}
.tagline{top:130px;color:var(--orange);font-size:16.5px}
.para{font-size:15px;line-height:28.5px;color:var(--body)}
.about .p1{top:172px;left:165px;width:870px}
.about .p2{top:300px;left:165px;width:870px}

/* services */
.services{top:1138px;left:0;width:1200px;height:466px;background:var(--dark)}
.services h2{top:60px;color:#fff}
.services .sub{top:130px;color:#fff;font-size:16px}
.svc{top:182px;width:320px;text-align:center}
.svc svg{display:block;margin:0 auto;stroke:#fff;fill:none;stroke-width:2.4}
.svc h3{margin-top:30px;color:var(--orange);font-weight:500;font-size:21px;line-height:28px}
.svc p{margin-top:8px;color:#fff;font-size:14px;line-height:29px}
.arrow{top:282px}

/* approach */
.approach{top:1604px;left:0;width:1200px;height:516px;background:linear-gradient(90deg,#f2e9fb 0%,#fff 18%)}
.approach .photo{left:74px;top:69px;width:512px;height:378px;background:linear-gradient(135deg,#c7ccd6 0%,#8e9ab0 50%,#4d5f80 100%)}
.approach h2{left:614px;top:120px}
.approach .p1{left:614px;top:185px;width:500px}
.approach .p2{left:614px;top:308px;width:500px}

/* banner */
.banner{top:2120px;left:0;width:1200px;height:421px;background:linear-gradient(100deg,#1d3b1e 0%,#3b4b22 30%,#8a4a18 65%,#d9661b 100%)}
.banner h2{top:103px;color:#fff;font-size:30px;line-height:35px}
.banner .para{top:196px;left:165px;width:870px;color:#fff}

/* testimonials */
.reviews{top:2541px;left:0;width:1200px;height:602px}
.reviews h2{top:55px}
.reviews .sub{top:126px;font-size:15.5px}
.card{top:187px;width:330px;height:253px;border:1.5px solid var(--line);text-align:center}
.card .q{margin-top:20px;color:var(--orange);font-size:90px;font-weight:600;line-height:70px;height:55px;overflow:hidden}
.card p{margin:12px 22px 0;font-size:14.5px;line-height:28px}
.who{top:468px;width:330px;text-align:center}
.who b{display:block;font-weight:600;color:var(--ink);font-size:16px}
.stars{margin-top:6px;color:var(--orange);font-size:17px;letter-spacing:2px}

/* contact */
.contact{top:3143px;left:0;width:1200px;height:566px;background:linear-gradient(135deg,#263039 0%,#1d242b 50%,#2a343b 100%)}
.contact h2{top:50px;color:#fff}
.contact .line{top:131px;color:#fff;font-size:15px;display:flex;justify-content:center;align-items:center;gap:8px}
.field{left:299px;width:602px;height:35px;background:#fff;color:#555;font-size:12px;padding:10px 14px}
.submit{left:524px;top:465px;width:151px;height:37px;background:var(--orange);color:#fff;font-weight:600;font-size:18px;text-align:center;line-height:37px}

/* footer */
.footer{top:3709px;left:0;width:1200px;height:265px}
.footer .logo{left:74px;top:80px;color:var(--ink)}
.footer .col{font-size:14.5px;line-height:25.5px;color:var(--ink)}
.social{top:78px;width:22px;height:22px;border-radius:4px;background:#333}
.copy{top:210px;font-size:12.5px;color:var(--ink)}
</style>
</head>
<body>

<header class="abs hero" role="img" aria-label="Photo of a technician in gloves cleaning an office desk">
  <div class="abs logo">KLORVEST</div>
  <nav class="abs nav">
    <a class="active">Home</a><a>About</a><a>Our Approach</a><a>Services &#8964;</a><a>Contact Us</a>
  </nav>
  <h1 class="abs center">We measure so the Business Owner can<br>Manage their Environments.</h1>
</header>

<section class="abs about">
  <h2 class="abs center">About Klorvest</h2>
  <p class="abs center tagline">We provide a service to electronically measure cleanliness of any surface and a value added disinfecting fogging surface.</p>
  <p class="abs para center p1">Lorem ipsum dolor sit amet, consectetur adipiscing elit. Integer auctor feugiat libero vitae tincidunt. Ut varius malesuada ex at<br>porta. Quisque augue mauris, dignissim sed velit eget, finibus porta urna. Suspendisse eget tempor risus, et imperdiet nisi.<br>Proin rhoncus, tellus sagittis rutrum aliquam, est ipsum vestibulum leo, vel tempor orci lacus ut nunc. Vivamus aliquet lectus nisl,<br>vitae efficitur nisl dignissim quis.</p>
  <p class="abs para center p2">Class aptent taciti sociosqu ad litora torquent per conubia nostra, per inceptos himenaeos. Sed cursus turpis sed lectus interdum,<br>sed ullamcorper nunc malesuada. Sed nec est vel arcu sodales egestas sit amet vel nulla.</p>
  <div class="dots" style="top:151px"><span class="on"></span><span></span><span></span><span></span><span></span></div>
</section>

<section class="abs services">
  <h2 class="abs center">Our Services</h2>
  <p class="abs center sub">Morbi id congue nibhhasellus maximus nisl ante, ut dictum felis.</p>
  <svg class="abs arrow" style="left:72px" width="16" height="24" viewBox="0 0 16 24"><path d="M12 3 3 12l9 9" stroke="#fff" stroke-width="3" fill="none"/></svg>
  <svg class="abs arrow" style="left:1112px" width="16" height="24" viewBox="0 0 16 24"><path d="M4 3l9 9-9 9" stroke="#fff" stroke-width="3" fill="none"/></svg>
  <div class="abs svc" style="left:79px">
    <svg width="64" height="60" viewBox="0 0 64 60"><path d="M4 30 32 6l28 24M12 24v32h40V24M26 56V40h12v16M18 30h8v7h-8zM38 30h8v7h-8z"/></svg>
    <h3>Residential</h3>
    <p>Nullam ultrices placerat libero, in tristique<br>massa euismod eget. Suspendisse<br>semper sapien</p>
  </div>
  <div class="abs svc" style="left:438px">
    <svg width="64" height="60" viewBox="0 0 64 60"><path d="M6 4h52l4 14H2zM2 18c0 5 10 5 10 0 0 5 10 5 10 0 0 5 10 5 10 0 0 5 10 5 10 0 0 5 10 5 10 0 0 5 10 5 10 0M8 24v32h48V24M14 32h14v24H14M36 32h14v12H36"/></svg>
    <h3>Commercial</h3>
    <p>Nullam ultrices placerat libero, in tristique<br>massa euismod eget. Suspendisse<br>semper sapien</p>
  </div>
  <div class="abs svc" style="left:798px">
    <svg width="96" height="60" viewBox="0 -2 96 60"><path d="M4 6h80l8 14v24H4zM10 12h16v12H10zM32 12h16v12H32zM54 12h12v28H54zM72 12h10l6 12H72zM4 30h50"/><circle cx="24" cy="46" r="6"/><circle cx="74" cy="46" r="6"/></svg>
    <h3>Transportation</h3>
    <p>Nullam ultrices placerat libero, in tristique<br>massa euismod eget. Suspendisse<br>semper sapien</p>
  </div>
  <div class="dots" style="top:165px"><span style="background:#fff"></span><span class="on"></span><span style="background:#fff"></span><span style="background:#fff"></span><span style="background:#fff"></span></div>
</section>

<section class="abs approach">
  <div class="abs photo" role="img" aria-label="Photo of a lab worker in protective suit holding a swab test tube"></div>
  <h2 class="abs">Our Approach</h2>
  <p class="abs para p1">Lorem ipsum dolor sit amet, consectetur adipiscing elit. Integer auctor feugiat libero vitae tincidunt. Ut varius malesuada ex at porta. Quisque augue mauris, dignissim sed velit eget, finibus porta urna. Suspendisse eget tempor risus, et imperdiet nisi.</p>
  <p class="abs para p2">Proin rhoncus, tellus sagittis rutrum aliquam, est ipsum vestibulum leo, vel tempor orci lacus ut nunc. Vivamus aliquet lectus nisl, vitae efficitur nisl dignissim quis.</p>
  <div class="dots" style="top:190px"><span></span><span></span><span class="on"></span><span></span><span></span></div>
</section>

<section class="abs banner" role="img" aria-label="Photo of a worker in protective gear using a green disinfecting fogger">
  <h2 class="abs center">We provide a service to electronically measure cleanliness of any surface<br>and a value added disinfecting fogging surface.</h2>
  <p class="abs para center">Lorem ipsum dolor sit amet, consectetur adipiscing elit. Integer auctor feugiat libero vitae tincidunt. Ut varius malesuada ex at<br>porta. Quisque augue mauris, dignissim sed velit eget, finibus porta urna. Suspendisse eget tempor risus, et imperdiet nisi.<br>Proin rhoncus, tellus sagittis rutrum aliquam, est ipsum vestibulum leo, vel tempor orci lacus ut nunc. Vivamus aliquet lectus nisl,<br>vitae efficitur nisl dignissim quis.</p>
</section>

<section class="abs reviews">
  <h2 class="abs center">What People are Saying</h2>
  <p class="abs center sub">Lorem ipsum dolor sit amet, consectetur adipiscing elit. Integer auctor feugiat libero vitae tincidunt.</p>
  <div class="abs card" style="left:74px"><div class="q">&ldquo;</div><p>&ldquo; Lorem ipsum dolor sit amet, consectetur adipiscing elit. Integer auctor feugiat libero vitae tincidunt. Ut varius malesuada ex at porta maximus nisl ante, ut dictum felis luctus..&rdquo;</p></div>
  <div class="abs card" style="left:435px"><div class="q">&ldquo;</div><p>&ldquo; Lorem ipsum dolor sit amet, consectetur adipiscing elit. Integer auctor feugiat libero vitae tincidunt. Ut varius malesuada ex at porta maximus nisl ante, ut dictum felis luctus..&rdquo;</p></div>
  <div class="abs card" style="left:796px"><div class="q">&ldquo;</div><p>&ldquo; Lorem ipsum dolor sit amet, consectetur adipiscing elit. Integer auctor feugiat libero vitae tincidunt. Ut varius malesuada ex at porta maximus nisl ante, ut dictum felis luctus..&rdquo;</p></div>
  <div class="abs who" style="left:74px"><b>Name Heading</b><div class="stars">★★★★★</div></div>
  <div class="abs who" style="left:435px"><b>Name Heading</b><div class="stars">★★★★★</div></div>
  <div class="abs who" style="left:796px"><b>Name Heading</b><div class="stars">★★★★★</div></div>
  <div class="dots" style="top:221px"><span></span><span></span><span></span><span class="on"></span><span></span></div>
</section>

<section class="abs contact">
  <h2 class="abs center">Contact Us</h2>
  <div class="abs center line">
    <svg width="14" height="14" viewBox="0 0 24 24"><path fill="#fff" d="M6.6 10.8a15 15 0 0 0 6.6 6.6l2.2-2.2c.3-.3.7-.4 1-.2 1.1.4 2.3.6 3.6.6.6 0 1 .4 1 1V20c0 .6-.4 1-1 1A17 17 0 0 1 3 4c0-.6.4-1 1-1h3.5c.6 0 1 .4 1 1 0 1.3.2 2.5.6 3.6.1.3 0 .7-.2 1z"/></svg>
    <span>1-800-555-0148 &nbsp;|&nbsp;</span>
    <svg width="15" height="12" viewBox="0 0 20 16"><path fill="#fff" d="M0 0h20v16H0zM2 2v1l8 6 8-6V2z"/></svg>
    <span>hello@klorvest.example</span>
  </div>
  <div class="abs field" style="top:180px">Name</div>
  <div class="abs field" style="top:228px">Email Address</div>
  <div class="abs field" style="top:274px">Phone</div>
  <div class="abs field" style="top:320px;height:122px">Message</div>
  <div class="abs submit">Submit</div>
  <div class="dots light" style="top:214px"><span></span><span></span><span></span><span></span><span></span></div>
</section>

<footer class="abs footer">
  <div class="abs logo">KLORVEST</div>
  <p class="abs col" style="left:342px;top:62px;width:240px">Nullam ultrices placerat libero, in tristique massa euismod eget. Suspendisse semper sapien eget enim sed mauris.</p>
  <p class="abs col" style="left:646px;top:62px">218 Larkmoor Avenue<br>Fenwick, CA 94302</p>
  <p class="abs col" style="left:646px;top:121px;display:flex;align-items:center;gap:18px">
    <svg width="12" height="12" viewBox="0 0 24 24"><path fill="#222" d="M6.6 10.8a15 15 0 0 0 6.6 6.6l2.2-2.2c.3-.3.7-.4 1-.2 1.1.4 2.3.6 3.6.6.6 0 1 .4 1 1V20c0 .6-.4 1-1 1A17 17 0 0 1 3 4c0-.6.4-1 1-1h3.5c.6 0 1 .4 1 1 0 1.3.2 2.5.6 3.6.1.3 0 .7-.2 1z"/></svg>555-019-2736</p>
  <div class="abs social" style="left:920px"></div>
  <div class="abs social" style="left:960px"></div>
  <p class="abs center copy">Copyright © 2020 CompanyName All rights reserved.</p>
</footer>

</body>
</html>
```